Business Card Design

We are a law firm which provides services to creditors.....we do collection litigation. I am wide open on suggestions. I was thinking of a square card? Alternatively, a vertically oriented standard card or a folded card.....something unique. I would like to use my firm logo and beyond that, I am open for any and all suggestions. I'm uncertain if the complete log is uploaded? If not, please let me email it to you.

Industry/Entity Type

Law Firm

Contact Information for Business Card

Hart, Crane & Dobbs, P.C.
Tom Dobbs, Lawyer
4387 N Larkspur Ave
Oklahoma City, OK 73924
tdobbs@HcdCounsel.com
www.HcdCounsel.com
mobile: 405-382-7914

```html
<!DOCTYPE html>
<html lang="en">
<head>
<meta charset="utf-8">
<title>Hart, Crane &amp; Dobbs, P.C. — Business Card</title>
<link href="https://fonts.googleapis.com/css2?family=Arimo:wght@400;700&display=swap" rel="stylesheet">
<style>
  :root {
    --page-bg: #e9e7e3;
    --card-white: #ffffff;
    --card-shade: #f1f1f1;
    --firm-green: #1f9a58;
    --firm-green-dark: #15804a;
    --text-gray: #3c3c3c;
    --text-dark: #222222;
    --pattern-light: #f3f2f0;
    --pattern-mid: #e4e2df;
  }
  * { box-sizing: border-box; margin: 0; padding: 0; }
  html, body {
    width: 1200px; height: 885px; overflow: hidden;
    background: var(--page-bg);
    font-family: "Arimo", Arial, sans-serif;
  }
  .canvas {
    position: relative; width: 1200px; height: 885px;
  }
  .card {
    position: absolute; left: 300px; width: 600px; height: 343px;
    background: linear-gradient(135deg, var(--card-white) 55%, var(--card-shade));
    box-shadow: 0 6px 18px rgba(0,0,0,0.18);
    overflow: hidden;
  }
  .card--front { top: 70px; }
  .card--back { top: 472px; }

  /* Front */
  .front__band {
    position: absolute; left: 0; bottom: 0; width: 262px; height: 112px;
    background: linear-gradient(160deg, var(--firm-green), var(--firm-green-dark));
  }
  .front__firm {
    position: absolute; left: 140px; top: 34px;
    font-weight: 700; font-size: 31px; color: var(--text-gray); letter-spacing: 0.2px;
  }
  .front__mark {
    position: absolute; left: 26px; top: 205px;
    display: flex; align-items: center; gap: 8px;
    background: var(--card-white); padding: 7px 12px 7px 9px;
    font-weight: 700; font-size: 15px; color: var(--firm-green-dark);
  }
  .mark-dot {
    width: 16px; height: 16px; border-radius: 50%; background: var(--firm-green-dark);
  }
  .front__details { position: absolute; left: 300px; top: 112px; color: var(--text-dark); }
  .front__name { font-weight: 700; font-size: 24px; color: var(--firm-green); }
  .front__title { font-weight: 700; font-size: 15px; margin-top: 2px; }
  .front__address { font-size: 15px; line-height: 20px; margin-top: 16px; }
  .front__contact { margin-top: 14px; font-size: 15px; line-height: 21px; }
  .contact-row { display: flex; align-items: center; gap: 8px; }
  .contact-row svg { width: 14px; height: 14px; flex: none; }
  .front__web {
    position: absolute; left: 300px; bottom: 36px; font-size: 16px; color: var(--text-dark);
  }

  /* Back */
  .back__pattern {
    position: absolute; inset: 0;
    background: radial-gradient(circle at 50% 45%, var(--pattern-light) 25%, var(--pattern-mid) 100%);
  }
  .back__mark {
    position: absolute; left: 50%; top: 118px; transform: translateX(-50%);
    display: flex; align-items: center; gap: 10px;
    font-weight: 700; font-size: 26px; color: var(--firm-green-dark); white-space: nowrap;
  }
  .back__mark .mark-dot { width: 24px; height: 24px; }
  .back__web {
    position: absolute; left: 0; right: 0; top: 205px; text-align: center;
    font-size: 30px; color: var(--text-gray); letter-spacing: 0.5px;
  }
</style>
</head>
<body>
<main class="canvas">
  <section class="card card--front" aria-label="Card front">
    <div class="front__band"></div>
    <h1 class="front__firm">Hart, Crane &amp; Dobbs, P.C.</h1>
    <div class="front__mark"><span class="mark-dot"></span>Hart, Crane &amp; Dobbs</div>
    <div class="front__details">
      <p class="front__name">Tom Dobbs</p>
      <p class="front__title">Lawyer</p>
      <p class="front__address">4387 N Larkspur Ave<br>Oklahoma City, OK 73924</p>
      <div class="front__contact">
        <p class="contact-row">
          <svg viewBox="0 0 14 14" aria-hidden="true"><rect width="14" height="14" fill="#1f9a58"/><rect x="4.5" y="2.5" width="5" height="9" rx="1" fill="none" stroke="#fff" stroke-width="1.2"/></svg>
          405-382-7914
        </p>
        <p class="contact-row">
          <svg viewBox="0 0 14 14" aria-hidden="true"><rect width="14" height="14" fill="#1f9a58"/><rect x="2.5" y="4" width="9" height="6" fill="none" stroke="#fff" stroke-width="1.1"/><path d="M2.5 4 L7 7.5 L11.5 4" fill="none" stroke="#fff" stroke-width="1.1"/></svg>
          tdobbs@HcdCounsel.com
        </p>
      </div>
    </div>
    <p class="front__web">www.HcdCounsel.com</p>
  </section>

  <section class="card card--back" aria-label="Card back">
    <div class="back__pattern" role="img" aria-label="Faint repeating pattern of the firm emblem in light grey"></div>
    <div class="back__mark"><span class="mark-dot"></span>Hart, Crane &amp; Dobbs</div>
    <p class="back__web">www.HcdCounsel.com</p>
  </section>
</main>
</body>
</html>
```